Quendra Website re-design with new logo and look

Refresh on current website. Incorporate new logo which is attached. We provide technology SAAS services to the healthcare space. Current website is at quendra.com but the new name is Quendra.com (see logo) Key considerations are as follows:
1. Incorporate a promo video location. I have a new video coming out similar to this one. https://www.portvane.net/gallery/41736520/Mobile-Application-Promo
2. Incorporate platform features section. as an example see this website where it has mini screens that call out various features ie; "all in one GCR platform" see webiste https://www.pelvox.io/
3. Add some color splash from the log throughout the website
4. Where possible use the text from our website Quendra.com where not possible use lorem ipsum and we will complete
5. use current theme colors
6. Please use your skills to make it more functional and useful and not replicate what we have.

Target Market(s)

Imaging centers and hospitals

Industry/Entity Type

Healthcare

Coding

Coded - Design and coding required

Number of Pages Required

5+ page

Font styles to use
Sans Serif

Requirements
Must have
• Note section in this website that shows features of the platform as you scoll down. See website https://www.pelvox.io/
Nice to have
• Professional look only, keep current color scheme but add in some splash of color from the logo
Should not have
• animated characters or cartoon drawings

```html
<!DOCTYPE html>
<html lang="en">
<head>
<meta charset="utf-8">
<title>Quendra — Empowering Health Systems</title>
<link href="https://fonts.googleapis.com/css2?family=Poppins:wght@400;500;600;700&display=swap" rel="stylesheet">
<style>
  :root{
    --teal-dark:#0b6f88;
    --teal:#138aa6;
    --teal-light:#35aec3;
    --ink:#111820;
    --white:#ffffff;
    --hero-deep:#04121a;
    --hero-mid:#0d3347;
    --hero-blue:#1a5f80;
  }
  *{box-sizing:border-box;margin:0;padding:0}
  html,body{width:1200px;height:867px;overflow:hidden;background:var(--white)}
  body{font-family:"Poppins",Arial,sans-serif;color:var(--ink);position:relative}

  .topbar{
    position:absolute;left:0;top:0;width:1200px;height:46px;
    background:linear-gradient(90deg,var(--teal-dark) 0%,var(--teal) 45%,var(--teal-light) 100%);
    color:var(--white);font-size:12.5px;font-weight:500;
  }
  .topbar .hours{position:absolute;left:61px;top:15px}
  .topbar .phone{position:absolute;left:330px;top:14px;display:flex;align-items:center;gap:7px}
  .topbar .social{position:absolute;left:990px;top:9px;display:flex;gap:15px}
  .topbar .social span{width:27px;height:27px;border-radius:50%;background:var(--white);display:block}

  .navbar{
    position:absolute;left:0;top:46px;width:1200px;height:70px;background:var(--white);
  }
  .brand{position:absolute;left:67px;top:22px;display:flex;align-items:center;gap:10px}
  .brand-dot{width:26px;height:26px;border-radius:50%;background:var(--teal)}
  .brand-name{font-size:22px;font-weight:600;letter-spacing:1.5px;color:var(--ink)}
  .nav-links{position:absolute;top:24px;left:0;list-style:none;font-size:15.5px;font-weight:500}
  .nav-links li{position:absolute;white-space:nowrap}
  .btn-contact{
    position:absolute;left:994px;top:9px;width:142px;height:52px;border-radius:12px;
    background:var(--teal);color:var(--white);font-size:15.5px;font-weight:600;
    display:flex;align-items:center;justify-content:center;
  }

  .hero{
    position:absolute;left:0;top:116px;width:1200px;height:751px;
    background:
      radial-gradient(ellipse at 78% 70%,var(--hero-blue) 0%,transparent 55%),
      radial-gradient(ellipse at 35% 55%,#163e52 0%,transparent 50%),
      linear-gradient(180deg,var(--hero-deep) 0%,var(--hero-mid) 100%);
  }
  .hero-copy{position:absolute;left:0;top:0;width:1200px;text-align:center;color:var(--white)}
  .eyebrow{position:absolute;left:0;width:1200px;top:290px;font-size:30px;font-weight:600}
  .headline{position:absolute;left:0;width:1200px;top:342px;font-size:74px;font-weight:700;letter-spacing:.5px;line-height:1.2}
  .lede{position:absolute;left:300px;width:600px;top:510px;font-size:14px;font-weight:500;line-height:20px}
  .btn-learn{
    position:absolute;left:531px;top:594px;width:137px;height:50px;border-radius:12px;
    background:var(--white);color:var(--ink);font-size:14.5px;font-weight:600;
    display:flex;align-items:center;justify-content:center;
  }
</style>
</head>
<body>
  <header class="topbar">
    <span class="hours">Monday &nbsp;- Friday: 8 :00 AM - 9 :00 PM</span>
    <span class="phone">
      <svg width="14" height="14" viewBox="0 0 24 24" aria-hidden="true"><path fill="#fff" d="M6.6 10.8a15.1 15.1 0 0 0 6.6 6.6l2.2-2.2a1 1 0 0 1 1-.25 11.4 11.4 0 0 0 3.6.57 1 1 0 0 1 1 1V20a1 1 0 0 1-1 1A17 17 0 0 1 3 4a1 1 0 0 1 1-1h3.5a1 1 0 0 1 1 1c0 1.25.2 2.45.57 3.57a1 1 0 0 1-.25 1z"/></svg>
      (555) 204-6618
    </span>
    <div class="social" aria-label="Social links"><span></span><span></span><span></span><span></span></div>
  </header>

  <nav class="navbar">
    <div class="brand"><span class="brand-dot"></span><span class="brand-name">QUENDRA</span></div>
    <ul class="nav-links">
      <li style="left:344px">Home</li>
      <li style="left:434px">About Us</li>
      <li style="left:546px">Services</li>
      <li style="left:653px">Benefits</li>
      <li style="left:758px">Platform</li>
    </ul>
    <a class="btn-contact">Contact Us</a>
  </nav>

  <section class="hero" role="img" aria-label="Dark blue-toned photo of a medical lab with a 3D printer and a technician at a monitor">
    <div class="hero-copy">
      <p class="eyebrow">Technology</p>
      <h1 class="headline">Empowering Health Systems</h1>
      <p class="lede">Our End To End Workflow Platform Is Purposely Built For Remote Access From Anywhere In The World While Providing.</p>
      <a class="btn-learn">Learn More</a>
    </div>
  </section>
</body>
</html>
```